Detail Shop Business card design

i need a business card design for my new detailing company called 'Brisk's Polish Works'. i want an all black and white design . simple, direct and to the point. i want the designer to choose a fitting font to match the logothe front should have logo, address, phone and email and the back side should have a slogan and text indicating that we offer services on anything including cars, trucks, motorcycles and RVs. slogan will read "we take pride in your ride"
maybe also very small on the back side the IG icon with Brisks_Polish_Works

phone 208.417.6352
address 3847 E Larkin Ave
Spokane WA 99214
email: BrisksPolish@mailvexo.com

Target Market(s)

all ages , auto enthusiasts

Industry/Entity Type

Automotive

Contact Information for Business Card

the front should have logo, address, phone and email and the back side should have a slogan and text indicating that we offer services on anything including cars, trucks, motorcycles and RVs. slogan will read "we take pride in your ride"

phone 208.417.6352
address 3847 E Larkin Ave
Spokane WA 99214

Colors
000000
ffffff

Requirements
Must have
• bold font and very simple design with good spacing
Nice to have
• anything creative from the designer indicating we service any types of vehicles
Should not have
• any colors ,

```html
<!DOCTYPE html>
<html lang="en">
<head>
<meta charset="utf-8">
<title>Brisk's Polish Works – Business Card</title>
<link rel="stylesheet" href="https://fonts.googleapis.com/css2?family=Lato:wght@400;900&family=Tinos&family=Italianno&display=swap">
<style>
  :root {
    --ink: #000000;
    --paper: #ffffff;
    --stage: #8a8a8a;
    --card-black: #050505;
    --shade: #1e1e1e;
    --rule: #000000;
  }
  * { margin: 0; padding: 0; box-sizing: border-box; }
  html, body {
    width: 1200px; height: 1200px; overflow: hidden;
    background: var(--stage);
  }
  .canvas { position: relative; width: 1200px; height: 1200px; }

  .card {
    position: absolute; top: 310px;
    width: 366px; height: 594px;
    overflow: hidden;
    box-shadow: 0 2px 6px rgba(0,0,0,0.35);
  }

  /* Front */
  .card-front { left: 233px; background: var(--paper); color: var(--ink); }
  .brand {
    position: absolute; top: 110px; left: 0; width: 100%;
    display: flex; flex-direction: column; align-items: center; gap: 18px;
  }
  .brand-mark {
    width: 96px; height: 96px; border-radius: 50%;
    border: 10px solid var(--ink);
  }
  .brand-name {
    font-family: "Lato", sans-serif; font-weight: 900;
    font-size: 28px; letter-spacing: 0.5px; color: var(--ink);
    text-align: center; line-height: 1.15;
  }
  .contact {
    position: absolute; top: 374px; left: 0; width: 100%;
    font-family: "Lato", sans-serif; font-size: 16px; line-height: 22px;
    text-align: center; color: var(--ink);
  }
  .contact-email { font-size: 15.5px; }
  .rule {
    width: 190px; height: 1px; background: var(--rule);
    margin: 12px auto 12px;
  }
  .rule-with-dot {
    display: flex; align-items: center; justify-content: center;
    gap: 6px; margin: 7px auto 2px;
  }
  .rule-with-dot .line { width: 82px; height: 1px; background: var(--rule); }
  .rule-with-dot .dot {
    width: 18px; height: 18px; border-radius: 50%; background: var(--ink);
  }

  /* Back */
  .card-back { left: 627px; background: var(--card-black); color: var(--paper); }
  .vehicle-art {
    position: absolute; left: 0; top: 150px; width: 100%; height: 444px;
    background: radial-gradient(ellipse at 25% 55%, var(--shade) 0%, rgba(30,30,30,0.6) 45%, rgba(5,5,5,0) 75%);
  }
  .services {
    position: absolute; top: 230px; left: 0; width: 100%;
    font-family: "Tinos", serif; font-size: 22.5px; line-height: 50.5px;
    text-align: center; text-transform: uppercase; letter-spacing: 0.3px;
  }
  .slogan {
    position: absolute; top: 505px; left: 0; width: 100%;
    font-family: "Italianno", cursive; font-size: 50px;
    text-align: center; white-space: nowrap;
  }
</style>
</head>
<body>
<main class="canvas">
  <section class="card card-front">
    <div class="brand">
      <span class="brand-mark" aria-hidden="true"></span>
      <span class="brand-name">Brisk's Polish Works</span>
    </div>
    <div class="contact">
      <p class="contact-phone">208.417.6352</p>
      <p class="contact-email">BrisksPolish@mailvexo.com</p>
      <div class="rule"></div>
      <p class="contact-street">3847 E Larkin Ave</p>
      <p class="contact-city">Spokane WA 99214</p>
      <div class="rule-with-dot"><span class="line"></span><span class="dot"></span><span class="line"></span></div>
      <p class="contact-handle">Brisks_Polish_Works</p>
    </div>
  </section>

  <section class="card card-back">
    <div class="vehicle-art" role="img" aria-label="Faint dark silhouette of a classic hot rod car"></div>
    <div class="services">
      <p>We offer services on</p>
      <p>including&nbsp; cars, trucks</p>
      <p>motorcycles and RVs.</p>
    </div>
    <p class="slogan">We take pride in your ride</p>
  </section>
</main>
</body>
</html>
```